Business Cards for Internet Security Company

Awesome designers! This is the opportunity to help design cards for a forward thinking network security company. They use threat information gathered from peer groups to make intelligent decisions on what threats are relevant and which arent. ( not that you need this to do designs, but just so you know where they are coming from. ) :-)

We'd like to see a two side design and the deliverables will be in illustrator 4. The logo is attached and the logo colors are attached in the JPG and I've attached a an eps of the logo and icon

Security

```html
<!DOCTYPE html>
<html lang="en">
<head>
<meta charset="utf-8">
<title>Kestrin Business Cards</title>
<link href="https://fonts.googleapis.com/css2?family=Exo+2:ital,wght@0,500;0,600;1,400;1,500&display=swap" rel="stylesheet">
<style>
  :root {
    --bg-top: #e4e4e6;
    --bg-bottom: #c9c9cc;
    --card-light: #eeeff1;
    --card-panel: #e6e8eb;
    --brand-blue: #155a93;
    --brand-sky: #3b8fd6;
    --ink-dark: #2d3036;
    --ink-light: #ffffff;
  }
  * { box-sizing: border-box; margin: 0; padding: 0; }
  html, body { width: 1200px; height: 949px; overflow: hidden; }
  body {
    background: linear-gradient(160deg, var(--bg-top), var(--bg-bottom));
    font-family: "Exo 2", sans-serif;
    position: relative;
  }
  .card {
    position: absolute;
    left: 250px;
    width: 700px;
    height: 400px;
    border-radius: 26px;
    overflow: hidden;
    box-shadow: 0 10px 26px rgba(0,0,0,.18);
  }
  .card--front { top: 48px; background: var(--card-light); }
  .card--back { top: 496px; background: var(--card-panel); }

  .wordmark {
    display: flex;
    align-items: center;
    gap: 14px;
    color: var(--brand-blue);
    font-weight: 600;
    font-size: 78px;
    line-height: 1;
    letter-spacing: 1px;
  }
  .wordmark__dot {
    width: 46px; height: 46px;
    border-radius: 50%;
    background: var(--brand-sky);
    flex: none;
  }
  .card--front .wordmark {
    position: absolute;
    left: 0; right: 0; top: 128px;
    justify-content: center;
  }
  .card--front .website {
    position: absolute;
    left: 0; right: 0; top: 250px;
    text-align: center;
    color: var(--ink-dark);
    font-size: 18px;
    font-weight: 500;
    font-style: italic;
    letter-spacing: 2px;
  }

  .card--back .band {
    position: absolute;
    left: 0; right: 0; top: 108px; bottom: 0;
    background: var(--brand-blue);
  }
  .card--back .wordmark {
    position: absolute;
    left: 96px; top: 30px;
    font-size: 74px;
  }
  .identity {
    position: absolute;
    left: 62px; top: 124px;
    color: var(--ink-light);
    font-style: italic;
    display: flex; align-items: baseline; gap: 22px;
  }
  .identity__name { font-size: 21px; letter-spacing: 2px; font-weight: 500; }
  .identity__role { font-size: 12px; letter-spacing: 1.5px; }

  .contact {
    position: absolute;
    display: flex; align-items: flex-start; gap: 12px;
    color: var(--ink-light);
    font-style: italic;
    font-size: 19px;
    letter-spacing: 1px;
    line-height: 1.2;
  }
  .contact svg { width: 24px; height: 24px; flex: none; margin-top: 1px; }
  .contact--phone { left: 62px; top: 182px; font-size: 22px; }
  .contact--email { left: 62px; top: 240px; }
  .contact--address { left: 388px; top: 272px; font-size: 17px; }
  .contact--web { left: 388px; top: 330px; font-size: 17px; }
</style>
</head>
<body>

<section class="card card--front" aria-label="Card front">
  <div class="wordmark"><span class="wordmark__dot"></span>Kestrin</div>
  <p class="website">www.kestrin.net</p>
</section>

<section class="card card--back" aria-label="Card back">
  <div class="band"></div>
  <div class="wordmark"><span class="wordmark__dot"></span>Kestrin</div>

  <div class="identity">
    <span class="identity__name">ALAN MERCER</span>
    <span class="identity__role">FOUNDER</span>
  </div>

  <div class="contact contact--phone">
    <svg viewBox="0 0 24 24" fill="none" stroke="#fff" stroke-width="1.6"><circle cx="12" cy="12" r="10.5"/><path d="M9 7c-1 1-1 3 1 6s4 4 5 4l1-1.5-2-1.5-1 .8c-1-.5-2-2-2.3-3l.8-1-1.5-2z" fill="#fff" stroke="none"/></svg>
    <span>012 555 0148</span>
  </div>

  <div class="contact contact--email">
    <svg viewBox="0 0 24 24" fill="none" stroke="#fff" stroke-width="1.6"><circle cx="12" cy="12" r="10.5"/><rect x="7" y="8.5" width="10" height="7" rx="1" fill="#fff" stroke="none"/><path d="M7 9l5 3.5L17 9" stroke="#155a93" stroke-width="1.2"/></svg>
    <span>hello@kestrin.net</span>
  </div>

  <div class="contact contact--address">
    <svg viewBox="0 0 24 24" fill="none" stroke="#fff" stroke-width="1.6"><circle cx="12" cy="12" r="10.5"/><path d="M12 18s-4-4.5-4-7.5a4 4 0 0 1 8 0c0 3-4 7.5-4 7.5z" fill="#fff" stroke="none"/><circle cx="12" cy="10.5" r="1.4" fill="#155a93" stroke="none"/></svg>
    <span>417 9th floor,Harbor<br>Lane Road NTK</span>
  </div>

  <div class="contact contact--web">
    <svg viewBox="0 0 24 24" fill="none" stroke="#fff" stroke-width="1.4"><circle cx="12" cy="12" r="10.5"/><circle cx="12" cy="12" r="6"/><path d="M6 12h12M12 6v12M8 8.5h8M8 15.5h8"/></svg>
    <span>www.kestrin.net</span>
  </div>
</section>

</body>
</html>
```